Boutique Real Estate Brokerage Tessly Realty Website Design

Winning designer work on migrate as well through nest ferry.
We need a new website as an informational hub to aid our print and digital strategy as well as showing that we are located in Brooklyn and Florida. I have a boutique real estate brokerage and advisory firm specializing in residential leasing, multifamily sales and 1031 Exchange appropriation. This won't be a portal to search properties, it will be a place for information. I'd like space for an ebook to be downloaded and information on my probate sales and multifamily leasing marketing campaigns. I included my logo and will leave it up to the designer to come up with colors to match it. I have also attached verbiage for each page. The final design should have a modern high end look that reflects gentrifying Brooklyn as well as beautiful Florida.
Thank you!
Target Market(s)
Owners of income producing real estate and develop-able land in Brooklyn, NY and Florida.
Industry/Entity Type
Real Estate
Coding
Coded - Design and coding required
Number of Pages Required
5+ page
Colors
Designer to choose colors to be used in the design.
Requirements
Must have
- A modern elegant look
Nice to have
- pictures of brooklyn and florida
Should not have
- real estate search pages

```html
<!DOCTYPE html>
<html lang="en">
<head>
<meta charset="utf-8">
<title>Tessly Realty</title>
<link href="https://fonts.googleapis.com/css2?family=Mulish:wght@300;400;600&family=Open+Sans:wght@400;600&display=swap" rel="stylesheet">
<style>
:root{
  --black:#050505;
  --ink:#222;
  --muted:#555;
  --light:#e8e8e8;
  --white:#fff;
  --line:#dcdcdc;
  --footer:#2a2a2a;
  --footer-text:#bdbdbd;
  --field:#d9d9d9;
  --dark-btn:#2f2f2f;
}
*{box-sizing:border-box;margin:0;padding:0}
html,body{width:1200px;height:3077px;overflow:hidden}
body{font-family:"Mulish",sans-serif;color:var(--ink);background:var(--light);position:relative}
section,header,footer{position:absolute;left:0;width:1200px}
.wrap{position:absolute;left:144px;width:912px}

/* header */
.site-header{top:0;height:112px;background:var(--black);color:var(--white)}
.brand{position:absolute;left:145px;top:30px;display:flex;align-items:center;gap:14px}
.brand-mark{width:50px;height:50px;background:#8a8a8a}
.brand-name{font-size:17px;font-weight:600;letter-spacing:1px;color:#cfcfcf;text-transform:uppercase}
.contact-bar{position:absolute;right:145px;top:24px;display:flex;gap:26px;font-size:15px;color:#d0d0d0}
.contact-bar span{display:flex;align-items:center;gap:8px}
.main-nav{position:absolute;right:145px;top:70px;display:flex;gap:34px;font-size:14px;text-transform:uppercase}
.main-nav a{color:var(--white);text-decoration:none}
.main-nav a.active{text-decoration:underline;text-underline-offset:5px}

/* hero */
.hero{top:112px;height:503px;background:linear-gradient(100deg,#3a2a22 0%,#6a4a3a 30%,#4d4a44 60%,#2f3a2a 85%,#5a6a4a 100%)}
.hero-overlay{position:absolute;inset:0;background:rgba(0,0,0,.25)}
.hero-title{position:absolute;top:185px;width:100%;text-align:center;color:var(--white);font-size:31px;line-height:40px;font-weight:400}
.btn{display:inline-block;background:var(--white);color:var(--ink);font-size:14px;padding:8px 15px;border-radius:3px;border:1px solid #ccc}
.hero .btn{position:absolute;left:552px;top:275px}
.arrow{position:absolute;top:238px}

/* help */
.help{top:615px;height:515px;background:var(--light)}
h2{font-weight:400;font-size:33px;text-align:center;color:var(--ink)}
.help h2{position:absolute;top:75px;width:100%}
.service{position:absolute;top:135px;width:300px;height:302px}
.service .cap{position:absolute;bottom:0;left:0;right:0;height:44px;background:rgba(60,60,60,.72);color:#e6e6e6;font-size:16px;font-weight:300;text-align:center;line-height:44px}

/* ebook */
.ebook{top:1130px;height:358px;background:linear-gradient(180deg,#3c3340 0%,#5a4048 40%,#2f3140 75%,#2a2a35 100%);color:var(--white);text-align:center}
.ebook h2{color:var(--white);font-size:31px;line-height:40px;position:absolute;top:72px;width:100%}
.ebook p{position:absolute;top:165px;left:145px;width:910px;font-family:"Open Sans",sans-serif;font-size:13px;line-height:22px;color:#e8e8e8}
.ebook .btn{position:absolute;left:552px;top:243px}

/* mortgage */
.tools{top:1488px;height:555px;background:var(--light)}
.tools h2{position:absolute;top:72px;width:100%}
.tool{position:absolute;top:175px;width:300px;height:302px;background:var(--white)}
.tool-icon{position:absolute;left:110px;top:-40px;width:80px;height:80px;border-radius:50%;background:#2b2b2b;display:flex;align-items:center;justify-content:center}
.tool h3{position:absolute;top:48px;width:100%;text-align:center;font-weight:400;font-size:16px}
.rates{position:absolute;top:85px;left:0;width:100%;border-collapse:collapse;font-family:"Open Sans",sans-serif;font-size:11px}
.rates th{font-weight:400;font-size:14px;font-family:"Mulish",sans-serif;height:34px;border-bottom:1px solid var(--line)}
.rates td{height:40px;border-bottom:1px solid var(--line)}
.rates td:first-child{padding-left:16px}
.rates td:not(:first-child),.rates th:not(:first-child){text-align:center}
.small-btn{position:absolute;left:16px;top:253px;font-size:11px;padding:8px 12px;border:1px solid #bbb;border-radius:3px;background:var(--white)}
.label{position:absolute;left:16px;font-size:14px}
.select{position:absolute;left:16px;width:268px;height:34px;background:var(--field);border-radius:3px;font-size:14px;padding:8px 14px;display:flex;justify-content:space-between}
.zips{position:absolute;top:85px;left:0;width:100%;list-style:none;font-family:"Open Sans",sans-serif;font-size:12px}
.zips li{border-top:1px solid var(--line);height:24px;line-height:23px;padding-left:130px}

/* posts */
.posts{top:2043px;height:402px;background:linear-gradient(180deg,#2d3548 0%,#44506a 35%,#7a7e86 70%,#4a4642 100%)}
.posts h2{position:absolute;top:75px;width:100%;color:var(--white)}
.post{position:absolute;left:144px;top:130px;width:912px;height:195px;background:var(--light)}
.post-photo{position:absolute;left:0;top:0;width:320px;height:195px;background:linear-gradient(90deg,#4a6a3a 0%,#7a3a2a 45%,#9a4a30 100%)}
.post-body{position:absolute;left:348px;top:30px;width:540px}
.post-body h4{font-weight:400;font-size:18px;margin-bottom:8px}
.post-body .date{font-family:"Open Sans",sans-serif;font-size:11px;color:var(--muted);margin-bottom:14px}
.post-body p{font-family:"Open Sans",sans-serif;font-size:10px;line-height:17px;color:var(--muted)}
.post-body a{display:block;margin-top:2px;font-family:"Open Sans",sans-serif;font-size:10px;color:var(--ink);font-weight:600}

/* contact */
.contact{top:2445px;height:425px;background:var(--light)}
.contact h2{position:absolute;top:73px;width:100%}
.field{position:absolute;background:var(--white);font-family:"Open Sans",sans-serif;font-size:12px;padding:12px 14px;color:var(--ink)}
.submit{position:absolute;left:560px;top:312px;width:80px;height:36px;background:var(--dark-btn);color:var(--white);font-size:14px;text-align:center;line-height:36px;border-radius:3px}

/* footer */
.site-footer{top:2870px;height:207px;background:var(--footer);color:var(--footer-text);font-family:"Open Sans",sans-serif}
.site-footer h5{font-family:"Mulish",sans-serif;font-weight:400;font-size:15px;color:#e6e6e6;margin-bottom:12px}
.f-col{position:absolute;top:38px}
.f-col li{list-style:none;font-size:10px;line-height:21px;display:flex;align-items:center;gap:12px}
.f-links{display:grid;grid-template-columns:68px 60px}
.f-links span{font-size:10px;line-height:21px}
.social{display:flex;gap:20px;margin-left:2px}
.social i{width:14px;height:14px;border-radius:50%;background:#9a9a9a;display:block}
.f-rule{position:absolute;left:144px;top:148px;width:912px;border-top:1px solid #4a4a4a}
.copy{position:absolute;top:170px;width:100%;text-align:center;font-size:10px}
</style>
</head>
<body>

<header class="site-header">
  <div class="brand"><span class="brand-mark"></span><span class="brand-name">Tessly Realty</span></div>
  <div class="contact-bar">
    <span><svg width="13" height="13" viewBox="0 0 24 24"><path fill="#ccc" d="M6.6 10.8c1.4 2.8 3.8 5.1 6.6 6.6l2.2-2.2c.3-.3.7-.4 1-.2 1.1.4 2.3.6 3.6.6.6 0 1 .4 1 1V20c0 .6-.4 1-1 1C10.6 21 3 13.4 3 4c0-.6.4-1 1-1h3.5c.6 0 1 .4 1 1 0 1.3.2 2.5.6 3.6.1.3 0 .7-.2 1z"/></svg>516-555-0147</span>
    <span><svg width="14" height="11" viewBox="0 0 24 18"><path fill="#ccc" d="M0 0h24v18H0z"/><path fill="none" stroke="#050505" stroke-width="2" d="M1 1l11 9 11-9"/></svg>info@tesslyrealty.com</span>
  </div>
  <nav class="main-nav">
    <a class="active">Home</a><a>About Us</a><a>Services</a><a>Sign Up</a><a>Contact</a>
  </nav>
</header>

<section class="hero" role="img" aria-label="Brooklyn brownstone stoops along a tree lined street">
  <div class="hero-overlay"></div>
  <h1 class="hero-title">Assisting landlords increase profits<br>while decreasing the stress.</h1>
  <span class="btn">Read More</span>
  <svg class="arrow" style="left:48px" width="16" height="26" viewBox="0 0 16 26"><path d="M13 2L3 13l10 11" fill="none" stroke="#fff" stroke-width="3"/></svg>
  <svg class="arrow" style="left:1136px" width="16" height="26" viewBox="0 0 16 26"><path d="M3 2l10 11L3 24" fill="none" stroke="#fff" stroke-width="3"/></svg>
</section>

<section class="help">
  <h2>How We Can Help</h2>
  <div class="service" style="left:144px;background:linear-gradient(180deg,#f2f2f0,#c9c4bb 70%,#8a7a66)" role="img" aria-label="Bright apartment dining room"><div class="cap">Multi-Family Leasing</div></div>
  <div class="service" style="left:449px;background:linear-gradient(180deg,#9aa2aa,#8a7a6a 50%,#5a5048)" role="img" aria-label="Multifamily building with fire escapes"><div class="cap">Multi-Family Sales</div></div>
  <div class="service" style="left:755px;background:linear-gradient(180deg,#b8c8d8,#8a9a8a 45%,#6a7a5a)" role="img" aria-label="Aerial view of a Florida town"><div class="cap">Site Selection Advisory</div></div>
</section>

<section class="ebook" role="img" aria-label="Waterfront city skyline at dusk">
  <h2>e-Book for probate sales and<br>multifamily leasing marketing campaigns</h2>
  <p>Vivamus efficitur ex condimentum, malesuada eros eget, feugiat nibh. Sed tellus ex, imperdiet eget gravida sit amet, volutpat eget turpis. In nec ultricies est. Etiam mattis augue vehicula odio posuere, sit amet tempus lectus luctus. Nulla facilisi. Etiam vel massa elementum, bibendum tellus venenatis, feugiat massa. Curabitur venenatis lacinia ornare. Cras sollicitudin cursus dui eu placerat.</p>
  <span class="btn">Download</span>
</section>

<section class="tools">
  <h2>Mortgage Tools</h2>
  <div class="tool" style="left:144px">
    <div class="tool-icon"><svg width="30" height="26" viewBox="0 0 30 26"><path d="M2 2v22h26" fill="none" stroke="#fff" stroke-width="2.5"/><rect x="7" y="12" width="4" height="9" fill="#fff"/><rect x="13" y="7" width="4" height="14" fill="#fff"/><rect x="19" y="10" width="4" height="11" fill="#fff"/></svg></div>
    <h3>Mortgage Rates</h3>
    <table class="rates">
      <tr><th></th><th>Current</th><th>Last Week</th></tr>
      <tr><td>30 Year Fixed</td><td>4.19%</td><td>4.17%</td></tr>
      <tr><td>15 Year Fixed</td><td>3.62%</td><td>3.64%</td></tr>
      <tr><td>5/1 Adjustable</td><td>3.92%</td><td>3.97%</td></tr>
    </table>
    <span class="small-btn">Current Mortgage Rates</span>
  </div>
  <div class="tool" style="left:450px">
    <div class="tool-icon"><svg width="24" height="30" viewBox="0 0 24 30"><rect x="1" y="1" width="22" height="28" rx="2" fill="none" stroke="#fff" stroke-width="2"/><rect x="5" y="5" width="14" height="5" fill="#fff"/><g fill="#fff"><rect x="5" y="13" width="3" height="3"/><rect x="10.5" y="13" width="3" height="3"/><rect x="16" y="13" width="3" height="3"/><rect x="5" y="18" width="3" height="3"/><rect x="10.5" y="18" width="3" height="3"/><rect x="16" y="18" width="3" height="3"/><rect x="5" y="23" width="3" height="3"/><rect x="10.5" y="23" width="3" height="3"/><rect x="16" y="23" width="3" height="3"/></g></svg></div>
    <h3>Mortgage Calculator</h3>
    <span class="label" style="top:88px">Home Price</span>
    <div class="select" style="top:112px"><span>$</span><span>&#8693;</span></div>
    <span class="label" style="top:183px">Down Payment</span>
    <div class="select" style="top:207px"><span>$</span><span>&#8693;</span></div>
    <span class="small-btn">Continue</span>
  </div>
  <div class="tool" style="left:756px">
    <div class="tool-icon"><svg width="20" height="28" viewBox="0 0 20 28"><path d="M10 0C4.5 0 0 4.5 0 10c0 7.5 10 18 10 18s10-10.5 10-18C20 4.5 15.5 0 10 0z" fill="#fff"/><circle cx="10" cy="10" r="3.5" fill="#2b2b2b"/></svg></div>
    <h3>Coverage Areas</h3>
    <ul class="zips"><li>11221</li><li>11233</li><li>11238</li><li>11216</li><li>11207</li><li>11208</li></ul>
  </div>
</section>

<section class="posts" role="img" aria-label="Florida waterfront buildings under an evening sky">
  <h2>Latest Posts</h2>
  <svg class="arrow" style="left:56px;top:215px" width="14" height="24" viewBox="0 0 16 26"><path d="M13 2L3 13l10 11" fill="none" stroke="#fff" stroke-width="3"/></svg>
  <svg class="arrow" style="left:1128px;top:215px" width="14" height="24" viewBox="0 0 16 26"><path d="M3 2l10 11L3 24" fill="none" stroke="#fff" stroke-width="3"/></svg>
  <article class="post">
    <div class="post-photo" role="img" aria-label="Brooklyn brick row houses with greenery"></div>
    <div class="post-body">
      <h4>Brooklyn, NY To West Palm Beach Florida…The Best Of Both</h4>
      <div class="date">April, 19 - 2019 &nbsp;at&nbsp; 10:15 AM</div>
      <p>Tessly Realty NYC is a full service real estate brokerage firm located in Brooklyn, NY and West Palm Beach, FL. We specialize in multifamily sales and leasing, short sales and 1031 Exchange property appropriation. With more than 12 years of experience we have had transactions in every one of Brooklyn's zip codes…</p>
      <a>READ MORE</a>
    </div>
  </article>
</section>

<section class="contact">
  <h2>Contact Us</h2>
  <div class="field" style="left:144px;top:130px;width:298px;height:40px">Name</div>
  <div class="field" style="left:451px;top:130px;width:298px;height:40px">Email</div>
  <div class="field" style="left:758px;top:130px;width:298px;height:40px">Email</div>
  <div class="field" style="left:144px;top:180px;width:912px;height:120px">Message</div>
  <div class="submit">Submit</div>
</section>

<footer class="site-footer">
  <div class="f-col" style="left:144px">
    <h5>Contact Info</h5>
    <ul>
      <li><svg width="9" height="9" viewBox="0 0 24 24"><path fill="#bdbdbd" d="M6.6 10.8c1.4 2.8 3.8 5.1 6.6 6.6l2.2-2.2c.3-.3.7-.4 1-.2 1.1.4 2.3.6 3.6.6.6 0 1 .4 1 1V20c0 .6-.4 1-1 1C10.6 21 3 13.4 3 4c0-.6.4-1 1-1h3.5c.6 0 1 .4 1 1 0 1.3.2 2.5.6 3.6.1.3 0 .7-.2 1z"/></svg>561-555-0182</li>
      <li><svg width="10" height="8" viewBox="0 0 24 18"><path fill="#bdbdbd" d="M0 0h24v18H0z"/></svg>mara@tesslyrealty.com</li>
      <li><svg width="8" height="10" viewBox="0 0 20 28"><path d="M10 0C4.5 0 0 4.5 0 10c0 7.5 10 18 10 18s10-10.5 10-18C20 4.5 15.5 0 10 0z" fill="#bdbdbd"/></svg>482 Linden Ave, 3, Brooklyn, New York 11221</li>
    </ul>
  </div>
  <div class="f-col" style="left:610px">
    <h5>Links</h5>
    <div class="f-links"><span>Home</span><span>Sign up</span><span>About us</span><span>Contact</span><span>Services</span></div>
  </div>
  <div class="f-col" style="left:926px">
    <h5>Follow us on</h5>
    <div class="social"><i></i><i></i><i></i><i></i></div>
  </div>
  <div class="f-rule"></div>
  <div class="copy">Copyright © 2019 &nbsp;Tessly Realty. &nbsp; All rights reserved.</div>
</footer>

</body>
</html>
```